Web and Logo Design for eCommerce site

We're launching a sister brand and require a full design for the site.

The site must have an established feel and appeal to corporate and institutional buyers.
Updates

Just a note about the wireframe design:

The Search & Rescue / Coast Guard / NVDK, etc. in the header area aren't buttons or menu items, but rather just info (along the lines of a tagline).  Sort of a "who we serve" sort of thing.

Worth noting is that it's specifically geared towards LARGE BUYERS.  For example, a police force buying 200 headlamps and 85 pairs of gloves.  So they'll register + sign in and then add a bunch of items to a RFQ.

Aim for a professional, masculine design.

Target Market(s)

We will be selling outdoor gear to the military, law enforcement, fire and rescue and first responders.

Requirements
Must have
• We require:
- Logo (vector based)

Site:
- template page
* main site template, re-skinned version of our current site
* horizontal drop-down menu
- product listings page
* thumbnail view of products
- product details page
* including elements such as product image, color/size selector, descriptions and specs (again, based loosely on our current website)
- account management page
* illustrating basic data entry styles for text box, buttons, grid, etc.

The site needs to be given a responsive design, so 2 versions of each design should be presented for desktop + mobile views.

Additional funds are available if the designer is able to fully implement the designs into a responsive framework such as bootstrap.

Nice to have
• Clean, professional design similar to:

http://military.trailvexagear.com/gov/accessories/gloves.html

http://leaf.ombrivo.com/ProductFind.aspx?language=EN&category=Hardshell&subcat=Waterproof_Jackets

```html
<!DOCTYPE html>
<html lang="en">
<head>
<meta charset="utf-8">
<title>Tundrafield – Canada outdoor Pro Supply</title>
<link href="https://fonts.googleapis.com/css2?family=PT+Sans:wght@400;700&display=swap" rel="stylesheet">
<style>
:root{
  --red:#a3102a;
  --red-dark:#7c0a1d;
  --nav-grey:#6e7277;
  --panel-grey:#7f8a93;
  --dark:#3e3e3e;
  --footer:#3a3a3a;
  --text:#444;
  --muted:#8a8a8a;
  --line:#c9c9c9;
  --white:#fff;
}
*{box-sizing:border-box;margin:0;padding:0}
html,body{width:882px;height:1200px;overflow:hidden;background:var(--white)}
body{font-family:"PT Sans",sans-serif;color:var(--text);position:relative}
.abs{position:absolute}
/* header */
.brand{left:71px;top:14px}
.brand-name{font-size:21px;font-weight:400;color:var(--red);line-height:1}
.brand-sub{font-size:9px;color:#666;margin-top:3px}
.account-tab{left:566px;top:0;width:242px;height:30px;background:var(--red);clip-path:polygon(0 0,100% 0,97% 100%,3% 100%);color:var(--white);font-size:10.5px;display:flex;align-items:center;justify-content:center;gap:6px}
.account-tab b{font-size:12px}
.social{left:494px;top:40px;display:flex;gap:10px}
.social span{width:11px;height:11px;border-radius:50%;background:#666;display:block}
.tagline{left:615px;top:41px;font-size:8.5px;color:#555}
.serve-bar{left:71px;top:58px;width:737px;height:23px;background:linear-gradient(#b31531,var(--red-dark));color:var(--white);font-size:10.5px;display:flex;align-items:center;padding-left:11px;gap:17px}
.main-nav{left:71px;top:82px;width:737px;height:38px;background:linear-gradient(#7a7e83,var(--nav-grey));color:var(--white);font-size:10.5px;display:flex;align-items:center;box-shadow:0 8px 8px -6px rgba(0,0,0,.35)}
.main-nav .home{width:38px;height:38px;display:flex;align-items:center;justify-content:center;background:#63676c;margin-right:19px}
.main-nav ul{list-style:none;display:flex;gap:18px}
.main-nav .search{margin-left:auto;width:38px;height:38px;background:var(--red);display:flex;align-items:center;justify-content:center}
/* hero */
.hero{left:71px;top:140px;width:737px;height:314px;border:1px solid #bbb;display:flex}
.hero-photo{width:548px;height:100%;background:linear-gradient(160deg,#9fb7cf 0%,#e9eef3 35%,#dfe5ec 70%,#b36a3e 100%)}
.hero-panel{flex:1;background:var(--panel-grey);color:var(--white);padding:18px 18px 0 18px;position:relative}
.hero-panel h2{font-weight:400;font-size:18px;line-height:18px;margin-bottom:7px}
.hero-panel p{font-size:10px;line-height:23px;text-align:justify}
.btn-red{display:inline-block;background:var(--red);color:var(--white);font-size:10px;padding:6px 17px;margin-top:9px}
.hero-arrows{position:absolute;right:19px;bottom:17px;display:flex;gap:5px}
.hero-arrows span{width:20px;height:20px;background:var(--red);display:flex;align-items:center;justify-content:center}
/* categories */
.categories{left:71px;top:463px;width:184px}
.categories h3{height:33px;background:linear-gradient(#b31531,var(--red-dark));color:var(--white);font-size:10px;font-weight:700;padding:11px 10px}
.cat{background:var(--dark);border-bottom:1px solid #555;height:64px;padding:9px 10px 0 37px;position:relative;color:var(--white)}
.cat i{position:absolute;left:10px;top:10px;width:16px;height:14px;background:#9a9a9a;border-radius:3px}
.cat h4{font-size:13px;font-weight:700;line-height:15px}
.cat p{font-size:8.5px;line-height:11px;color:#e8e8e8;font-weight:400;text-align:justify;margin-top:2px}
.compare{left:67px;top:898px;width:188px;height:99px;border:1px solid #ddd;background:#f6f6f6;padding:10px 11px}
.compare h3{color:var(--red);font-size:13px;font-weight:700;padding-bottom:8px;border-bottom:3px double #ccc}
.compare p{font-size:13px;color:var(--muted);line-height:19px;margin-top:9px}
/* products */
.section-title{font-size:13px;color:var(--red);font-weight:400}
.pager{display:flex;gap:2px}
.pager span{width:16px;height:15px;background:#6d6d6d;display:flex;align-items:center;justify-content:center}
.grid{display:flex;gap:11px}
.card{width:125px;border:1px solid var(--line);text-align:center;position:relative;overflow:hidden}
.thumb{width:90px;height:110px;margin:8px auto 0;border-radius:12px}
.swatches{display:flex;justify-content:center;gap:5px;height:10px;margin-top:4px}
.swatches span{width:9px;height:9px}
.card .name{font-size:8px;color:#333;margin-top:6px}
.card .price{font-size:9.5px;font-weight:700;color:var(--red)}
.btn-cart{display:inline-block;background:#1c1c1c;color:var(--white);font-size:8px;padding:5px 10px;border-radius:2px;margin-top:6px}
.card .links{font-size:8px;color:var(--muted);line-height:11px;margin:5px 0 7px}
.badge{position:absolute;right:-14px;top:6px;width:50px;transform:rotate(45deg);background:var(--red);color:var(--white);font-size:7px;line-height:10px}
/* brands */
.divider{left:60px;top:1013px;width:757px;height:1px;background:#ddd}
.brands-title{left:70px;top:1026px;font-size:17px;color:var(--red);font-weight:400}
.brand-row{left:82px;top:1070px;width:720px;display:flex;justify-content:space-between;align-items:center;color:#8c8c8c;font-weight:700;font-size:14px}
/* footer */
.footer{left:0;top:1135px;width:882px;height:65px;background:var(--footer);color:var(--white)}
.footer-links{position:absolute;left:71px;top:12px;display:flex;gap:11px;font-size:10px}
.payments{position:absolute;left:71px;top:36px;display:flex;gap:14px;font-size:12px;font-weight:700;color:#6fa6e0}
.footer-social{position:absolute;left:710px;top:20px;display:flex;gap:9px}
.footer-social span{width:17px;height:17px;border-radius:2px;background:#4c6fa8}
.footer-social span:last-child{background:#e59a2c}
</style>
</head>
<body>

<header>
  <div class="abs brand">
    <div class="brand-name">Tundrafield</div>
    <div class="brand-sub">Canada outdoor Pro Supply</div>
  </div>
  <div class="abs account-tab">Sign up | Log in | Your shopping Cart <b>0</b></div>
  <div class="abs social"><span></span><span></span><span></span><span></span><span></span></div>
  <div class="abs tagline">Great Outdoor Gear for Canada's First Responders</div>
  <div class="abs serve-bar"><span>Search&amp;Rescue</span><span>Coast Guard</span><span>NVDK &nbsp;Fire Military</span><span>LawEnforcement</span></div>
  <nav class="abs main-nav">
    <span class="home"><svg width="14" height="12" viewBox="0 0 14 12"><path d="M7 0 0 6h2v6h4V8h2v4h4V6h2z" fill="#fff"/></svg></span>
    <ul><li>Rescue Gear Footwear</li><li>Clothing</li><li>Tents,Mats, Sleeping Bags</li><li>Camping Gear</li><li>Snow Sports</li><li style="margin-left:8px">Brands</li></ul>
    <span class="search"><svg width="13" height="13" viewBox="0 0 13 13"><circle cx="5" cy="5" r="3.8" fill="none" stroke="#fff" stroke-width="2"/><path d="M8 8l4 4" stroke="#fff" stroke-width="2"/></svg></span>
  </nav>
</header>

<section class="abs hero">
  <div class="hero-photo" role="img" aria-label="Snowboarders resting on a sunny ski slope"></div>
  <div class="hero-panel">
    <h2>Summit LT Jacket<br>FieldCam</h2>
    <p>Lorem ipsum dolor sit amet, consectetur adipisicing elit, sed do eiusmod tempor incididunt ut labore et dolore magna aliqua. Ut enim ad minim veniam, quis nostrud</p>
    <span class="btn-red">Read More</span>
    <div class="hero-arrows">
      <span><svg width="8" height="10"><path d="M6 1 2 5l4 4" stroke="#fff" stroke-width="2" fill="none"/></svg></span>
      <span><svg width="8" height="10"><path d="M2 1l4 4-4 4" stroke="#fff" stroke-width="2" fill="none"/></svg></span>
    </div>
  </div>
</section>

<aside class="abs categories">
  <h3>CATEGORIES</h3>
  <div class="cat"><i></i><h4>Rescue Gear</h4><p>Lorem ipsum dolor sit amet, consectetur adipisicing elit, sed do</p></div>
  <div class="cat"><i></i><h4>Footwear</h4><p>Lorem ipsum dolor sit amet, consectetur adipisicing elit, sed do</p></div>
  <div class="cat"><i></i><h4>Clothing</h4><p>Lorem ipsum dolor sit amet, consectetur adipisicing elit, sed do</p></div>
  <div class="cat" style="height:66px"><i></i><h4>Tents,Mats, Sleeping Bags</h4><p>Lorem ipsum dolor sit amet,</p></div>
  <div class="cat"><i></i><h4>Camping Gear</h4><p>Lorem ipsum dolor sit amet, consectetur adipisicing elit, sed do</p></div>
  <div class="cat" style="height:63px"><i></i><h4>Snow Sports</h4><p>Lorem ipsum dolor sit amet, consectetur adipisicing elit, sed do</p></div>
</aside>

<div class="abs compare">
  <h3>Compare Products</h3>
  <p>You have no items in your shopping cart.</p>
</div>

<h2 class="abs section-title" style="left:282px;top:461px">Latest Products</h2>
<div class="abs pager" style="left:773px;top:463px"><span><svg width="5" height="7"><path d="M4 0 1 3.5 4 7" stroke="#fff" fill="none"/></svg></span><span><svg width="5" height="7"><path d="M1 0l3 3.5L1 7" stroke="#fff" fill="none"/></svg></span></div>
<div class="abs grid" style="left:280px;top:486px">
  <div class="card"><span class="badge">New</span><div class="thumb" role="img" aria-label="Camouflage hardshell jacket" style="background:linear-gradient(#a89a72,#7d7456)"></div><div class="swatches"><span style="background:#111"></span><span style="background:#8c7b55"></span><span style="background:#4f5a63"></span></div><div class="name">Summit LT Jacket FieldCam</div><div class="price">$750.00</div><span class="btn-cart">Add To Cart</span><div class="links">Add to Wishlist<br>Add to Compare</div></div>
  <div class="card"><div class="thumb" role="img" aria-label="Black hardshell jacket" style="background:linear-gradient(#3a3a3a,#151515)"></div><div class="swatches"><span style="background:#111"></span><span style="background:#8c7b55"></span><span style="background:#4f5a63"></span></div><div class="name">Summit LT Jacket FieldCam</div><div class="price">$750.00</div><span class="btn-cart">Add To Cart</span><div class="links">Add to Wishlist<br>Add to Compare</div></div>
  <div class="card"><div class="thumb" role="img" aria-label="Ski goggles with orange lens" style="background:linear-gradient(#e7a13a,#4a4a4a)"></div><div class="swatches"></div><div class="name">Summit LT Jacket FieldCam</div><div class="price">$750.00</div><span class="btn-cart">Add To Cart</span><div class="links">Add to Wishlist<br>Add to Compare</div></div>
  <div class="card"><div class="thumb" role="img" aria-label="Green and black ski touring boot" style="background:linear-gradient(#8cc63f,#222 60%,#e8e8e8)"></div><div class="swatches"></div><div class="name">Summit LT Jacket FieldCam</div><div class="price">$750.00</div><span class="btn-cart">Add To Cart</span><div class="links">Add to Wishlist<br>Add to Compare</div></div>
</div>

<h2 class="abs section-title" style="left:280px;top:741px">Featured Products</h2>
<div class="abs pager" style="left:773px;top:743px"><span><svg width="5" height="7"><path d="M4 0 1 3.5 4 7" stroke="#fff" fill="none"/></svg></span><span><svg width="5" height="7"><path d="M1 0l3 3.5L1 7" stroke="#fff" fill="none"/></svg></span></div>
<div class="abs grid" style="left:280px;top:769px">
  <div class="card"><div class="thumb" role="img" aria-label="White snow helmet" style="background:linear-gradient(#f2f2f2,#d9d9d9 60%,#333)"></div><div class="swatches"></div><div class="name" style="margin-top:24px">Summit LT Jacket FieldCam</div><div class="price">$750.00</div><span class="btn-cart">Add To Cart</span><div class="links">Add to Wishlist<br>Add to Compare</div></div>
  <div class="card"><div class="thumb" role="img" aria-label="Turquoise and orange ski boot" style="height:124px;background:linear-gradient(#e8572a,#2bb3d1)"></div><div class="swatches"></div><div class="name" style="margin-top:10px">Summit LT Jacket FieldCam</div><div class="price">$750.00</div><span class="btn-cart">Add To Cart</span><div class="links">Add to Wishlist<br>Add to Compare</div></div>
  <div class="card"><div class="thumb" role="img" aria-label="Pair of black snowboards" style="height:124px;width:50px;background:linear-gradient(90deg,#1b1b1b,#3a3a3a)"></div><div class="swatches"></div><div class="name" style="margin-top:10px">Summit LT Jacket FieldCam</div><div class="price">$750.00</div><span class="btn-cart">Add To Cart</span><div class="links">Add to Wishlist<br>Add to Compare</div></div>
  <div class="card"><div class="thumb" role="img" aria-label="Black snowboard binding" style="height:124px;background:linear-gradient(#2a2a2a,#0f0f0f)"></div><div class="swatches"></div><div class="name" style="margin-top:10px">Summit LT Jacket FieldCam</div><div class="price">$750.00</div><span class="btn-cart">Add To Cart</span><div class="links">Add to Wishlist<br>Add to Compare</div></div>
</div>

<div class="abs divider"></div>
<h2 class="abs brands-title">Our Brands</h2>
<div class="abs brand-row"><span>Kindhaven</span><span>Brightroom</span><span style="font-size:20px">Vantor</span><span>Galleryon</span><span>Lensmark Studio</span><span>Orvela</span><span>Marlow Foto</span></div>

<footer class="abs footer">
  <div class="footer-links"><span>Rescue Gear Footwear</span><span>Clothing</span><span>Tents,Mats, Sleeping Bags</span><span style="margin-left:10px">Camping Gear</span><span style="margin-left:8px">Snow Sports</span><span style="margin-left:15px">Brands</span></div>
  <div class="payments"><span>Carda</span><span>Monecard</span><span>Nimbix</span><span>PayRiver</span></div>
  <div class="footer-social"><span></span><span style="background:#eee"></span><span></span><span></span></div>
</footer>

</body>
</html>
```